German Headhunter/ HR Consultancy needs Business Cards Design

We need a business Card Design for our Company in Stuttgart. We are specialized as Headhunter/ HR Consultancy in Placement of specialist and managers in permanent employment. Please refer to our business logo.

```html
<!DOCTYPE html>
<html lang="en">
<head>
<meta charset="utf-8">
<title>Talvora Personalberatung – Business Card</title>
<link href="https://fonts.googleapis.com/css2?family=Montserrat:wght@400;500;700&display=swap" rel="stylesheet">
<style>
  :root {
    --brand-blue: #3a55a7;
    --brand-grey: #96979b;
    --paper: #ffffff;
    --paper-shade: #e6e7ea;
    --ink: #111111;
    --stage: #2a2a2a;
    --faint-mark: #d3d7e3;
  }
  * { box-sizing: border-box; margin: 0; padding: 0; }
  html, body { width: 1200px; height: 1015px; overflow: hidden; }
  body {
    background: var(--stage);
    font-family: "Montserrat", Arial, sans-serif;
    display: flex;
    flex-direction: column;
    align-items: center;
    justify-content: center;
    gap: 60px;
  }
  .card {
    position: relative;
    width: 620px;
    height: 354px;
    overflow: hidden;
    box-shadow: 0 10px 30px rgba(0,0,0,.45);
  }

  /* Back side */
  .card--back {
    background: linear-gradient(160deg, var(--paper) 40%, var(--paper-shade) 100%);
  }
  .back__mark {
    position: absolute;
    left: 70px; top: 95px;
    width: 250px; height: 230px;
    background: var(--faint-mark);
    opacity: .7;
  }
  .back__logo {
    position: absolute;
    left: 190px; top: 120px;
    display: flex; align-items: center; gap: 16px;
    color: var(--brand-blue);
  }
  .back__url {
    position: absolute;
    right: 60px; bottom: 40px;
    color: var(--brand-blue);
    font-size: 15px;
    letter-spacing: 1.5px;
  }

  /* Shared wordmark */
  .wordmark__square {
    width: 52px; height: 52px;
    background: currentColor;
    flex: none;
  }
  .wordmark__name {
    font-weight: 700;
    line-height: 1;
  }
  .wordmark__name .line1 { display: block; font-size: 44px; letter-spacing: 2px; }
  .wordmark__name .line2 { display: block; font-size: 14.5px; letter-spacing: 1.5px; margin-top: 5px; }

  /* Front side */
  .card--front { background: var(--paper); }
  .front__top {
    position: absolute; inset: 0 0 auto 0;
    height: 170px;
    background: var(--brand-blue);
  }
  .front__logo {
    position: absolute;
    left: 160px; top: 52px;
    display: flex; align-items: center; gap: 16px;
    color: var(--paper);
  }
  .front__mid {
    position: absolute; left: 0; right: 0; top: 170px;
    height: 112px;
    background: var(--brand-grey);
    display: flex; align-items: center;
    padding: 0 40px 0 120px;
    color: var(--paper);
  }
  .person { text-align: right; padding-right: 24px; border-right: 1.5px solid var(--paper); }
  .person__name { font-size: 25px; font-weight: 700; }
  .person__role { font-size: 15px; font-weight: 500; margin-top: 2px; }
  .contacts { list-style: none; padding-left: 22px; font-size: 14px; line-height: 1.6; }
  .contacts li { display: flex; align-items: center; gap: 10px; }
  .contacts svg { width: 15px; height: 15px; fill: none; stroke: var(--paper); stroke-width: 1.6; }
  .front__address {
    position: absolute; left: 0; right: 0; top: 282px;
    height: 54px;
    display: flex; align-items: center; justify-content: center;
    font-size: 18px; color: var(--ink); letter-spacing: .5px;
  }
  .front__strip {
    position: absolute; left: 0; right: 0; bottom: 0;
    height: 18px; display: flex;
  }
  .front__strip .blue { flex: 0 0 58%; background: var(--brand-blue); }
  .front__strip .grey { flex: 1; background: var(--brand-grey); margin-left: 4px; }
</style>
</head>
<body>

  <section class="card card--back" aria-label="Card back">
    <div class="back__mark" aria-hidden="true"></div>
    <div class="back__logo">
      <span class="wordmark__square"></span>
      <span class="wordmark__name"><span class="line1">TALVORA</span><span class="line2">PERSONALBERATUNG</span></span>
    </div>
    <p class="back__url">www.talvora.example</p>
  </section>

  <section class="card card--front" aria-label="Card front">
    <div class="front__top"></div>
    <div class="front__logo">
      <span class="wordmark__square"></span>
      <span class="wordmark__name"><span class="line1">TALVORA</span><span class="line2">PERSONALBERATUNG</span></span>
    </div>
    <div class="front__mid">
      <div class="person">
        <p class="person__name">Lukas Berger</p>
        <p class="person__role">Managing Director</p>
      </div>
      <ul class="contacts">
        <li><svg viewBox="0 0 16 16"><path d="M4 1.5l2.5 3-1.5 1.8c.8 1.8 2 3 3.8 3.8l1.8-1.5 3 2.5-1.6 2.2C7.5 13.3 2.7 8.5 1.8 3.1z"/></svg>0711-555 0182</li>
        <li><svg viewBox="0 0 16 16"><rect x="1.5" y="3.5" width="13" height="9"/><path d="M1.5 3.5l6.5 5 6.5-5"/></svg>info@talvora.example</li>
        <li><svg viewBox="0 0 16 16"><circle cx="8" cy="8" r="6.5"/><ellipse cx="8" cy="8" rx="2.8" ry="6.5"/><path d="M1.5 8h13M2.5 5h11M2.5 11h11"/></svg>www.talvora.example</li>
      </ul>
    </div>
    <p class="front__address">Kornweg 12, 70173 Stuttgart, Germany</p>
    <div class="front__strip"><span class="blue"></span><span class="grey"></span></div>
  </section>

</body>
</html>
```